Substance abuse awareness flyer for school age kids

I am needing a flyer for school-age kids. What if it were designed to look like an Quorby with someone texting and the text bubbles were some of the text below with emojis? Maybe a text chain between to friends:

Maybe the first text bubble says "I'm thinking about using drugs and alcohol"
the next bubble: "Just say no!" ( perhaps a stop sign emoji ?)

"Talk to your parents, your teachers at school, or your doctor about how drugs and alcohol can harm you"

another text bubble "did you know that alcohol and drugs could lead to..."
then include some of the info below (see links for more info).
Where ever you get info, it must be cited.

this needs to be English on one side and Spanish on the other side and needs to include the logo attached.

The effects of substance abuse
RMQ: https://www.rmqhealthnet.org/plwtrk/vesk/features/teen-substance-use.html
Affect growth and development, especially brain development. Not able to focus at school or be around friends. https://www.halvenstudy.org/sites/default/files/youthguide_2.pdf
Leads to risky behaviors and lack of impulse control (dangerous activities) https://www.halvenstudy.org/sites/default/files/youthguide_2.pdf
Contribute to health problems as an adult: heart disease, high blood pressure, and trouble sleeping.

Target Market(s)

school age kids 9-20

Requirements
Must have
• Print ready: 8.5x11

```html
<!DOCTYPE html>
<html lang="en">
<head>
<meta charset="utf-8">
<title>Teen Substance Use Awareness Flyer</title>
<link href="https://fonts.googleapis.com/css2?family=Montserrat:wght@500;600;700;800&display=swap" rel="stylesheet">
<style>
  :root {
    --green: #47b24a;
    --lime: #bdd631;
    --sky: #74cde0;
    --maroon: #5e2433;
    --ink: #111111;
    --violet: #6a3f9e;
    --violet-deep: #3f3c86;
    --paper: #ffffff;
  }
  * { margin: 0; padding: 0; box-sizing: border-box; }
  html, body {
    width: 1044px; height: 1200px; overflow: hidden;
    background: var(--paper);
    font-family: "Montserrat", sans-serif;
    color: var(--ink);
  }
  .flyer {
    position: absolute; left: 58px; top: 0;
    width: 927px; height: 1200px;
    background: var(--paper);
    overflow: hidden;
  }
  .backdrop { position: absolute; inset: 0; }
  .bubble-text { position: absolute; line-height: 1.12; }
  .bubble-ask {
    left: 134px; top: 57px; font-size: 19px; font-weight: 500;
    text-transform: uppercase; letter-spacing: 0.5px;
  }
  .bubble-no { left: 481px; top: 164px; font-size: 25px; font-weight: 800; }
  .bubble-talk { left: 334px; top: 243px; width: 340px; font-size: 17.5px; font-weight: 600; }
  .bubble-facts { left: 290px; top: 411px; width: 390px; font-size: 19.5px; font-weight: 600; }
  .bubble-cite {
    position: absolute; right: 268px; top: 554px;
    font-size: 18px; font-weight: 700; color: var(--paper);
  }
  .brand {
    position: absolute; left: 752px; top: 58px; width: 150px;
    display: flex; align-items: center; gap: 8px;
  }
  .brand-dot { width: 16px; height: 16px; border-radius: 50%; background: var(--maroon); flex: none; }
  .brand-name { font-size: 14px; font-weight: 700; color: var(--maroon); line-height: 1.15; }
  .risks-tag {
    position: absolute; left: 0; top: 701px; width: 359px; height: 43px;
    background: var(--green); border-radius: 0 22px 22px 0;
    padding-left: 11px; display: flex; align-items: center;
    font-size: 23px; font-weight: 800; letter-spacing: 0.2px;
  }
  .risks-list {
    position: absolute; left: 10px; top: 762px; width: 520px;
    list-style: none; font-size: 16.5px; font-weight: 500; line-height: 1.33;
  }
  .risks-list li { padding-left: 12px; text-indent: -12px; margin-bottom: 13px; }
  .risks-list li::before { content: "- "; font-weight: 800; }
  .closing {
    position: absolute; left: 10px; top: 950px; width: 905px;
    font-size: 23.5px; font-weight: 800; line-height: 1.24; color: var(--maroon);
  }
  .slogan {
    position: absolute; left: 210px; top: 1130px; width: 503px; height: 59px;
    background: var(--green); border-radius: 30px;
    display: flex; align-items: center; justify-content: center;
    font-size: 27px; font-weight: 800;
  }
</style>
</head>
<body>
<main class="flyer">
  <svg class="backdrop" width="927" height="1200" viewBox="0 0 927 1200" aria-hidden="false">
    <path class="field" d="M0 0 H927 V846 C700 836 560 770 450 700 C340 630 200 606 0 608 Z" fill="var(--green)"/>
    <path class="field-edge" d="M927 846 C700 836 560 770 450 700 C340 630 200 606 0 608" fill="none" stroke="var(--maroon)" stroke-width="8"/>

    <rect class="figure-left" x="0" y="154" width="245" height="456" rx="60" fill="var(--violet)" role="img" aria-label="Illustration of a teen seen from behind, texting on a phone"/>
    <rect class="figure-right" x="700" y="325" width="240" height="505" rx="60" fill="var(--violet-deep)" role="img" aria-label="Illustration of a second teen seen from behind, reading a text on a phone"/>

    <g class="bubble-ask-shape" fill="var(--lime)">
      <rect x="119" y="21" width="335" height="113" rx="22"/>
      <polygon points="181,128 181,152 222,132"/>
    </g>
    <g class="bubble-reply-shapes" fill="var(--sky)">
      <rect x="470" y="141" width="207" height="76" rx="16"/>
      <polygon points="605,213 640,213 640,234"/>
      <rect x="317" y="222" width="364" height="133" rx="22"/>
      <polygon points="590,350 636,350 636,372"/>
      <rect x="267" y="381" width="414" height="217" rx="26"/>
      <polygon points="525,592 588,592 585,634"/>
    </g>
  </svg>

  <div class="brand">
    <span class="brand-dot"></span>
    <span class="brand-name">Larkfield Health Partners</span>
  </div>

  <p class="bubble-text bubble-ask">I'm thinking about using<br>drugs and alcohol</p>
  <p class="bubble-text bubble-no">JUST SAY NO!</p>
  <p class="bubble-text bubble-talk">Talk to your parents, your teachers at school, or your doctor about how drugs and alcohol can harm you.</p>
  <p class="bubble-text bubble-facts">Did you know that alcohol and drugs could lead to - The development of chronic diseases and other serious problems including: High blood pressure, heart disease, stroke, liver disease, and digestive problems.</p>
  <p class="bubble-cite">-rmqhealthnet.org</p>

  <h2 class="risks-tag">RISKS OF SUBSTANCE USE</h2>
  <ul class="risks-list">
    <li>Affect the growth and development of teens, especially brain development.</li>
    <li>Occur more frequently with other risky behaviors, such as unprotected sex and dangerous driving.</li>
    <li>Contribute to the development of adult health problems, such as heart disease, high blood pressure, and sleep disorders.</li>
  </ul>

  <p class="closing">Finally, the earlier teens start using substances, the greater their chances of continuing to use substances and developing substance use problems later in life. When teens begin drinking at an early age, they increase the chance of becoming addicted to or continuing to abuse substances later in life.</p>

  <p class="slogan">Don’t snort your life away</p>
</main>
</body>
</html>
```